Card design for orthopaedic surgeons working as The Brightwater Joint Centre

Business cards, letterhead

Colors

Designer to choose colors to be used in the design.

Requirements
Must have
• Late addition.
• Cards letterhead must have logos of
• Crestmoor Lindell College of Surgeons
• Varenwood Bone Health Association
Nice to have
• Back of card to have space for appointment time to be added by hand and some blank space for writing incidental other notes.

```html
<!DOCTYPE html>
<html lang="en">
<head>
<meta charset="utf-8">
<title>The Brightwater Joint Centre – Stationery</title>
<link href="https://fonts.googleapis.com/css2?family=Roboto:wght@300;400;500&display=swap" rel="stylesheet">
<style>
  :root {
    --navy: #022c45;
    --sky: #4fa7de;
    --paper: #ffffff;
    --backdrop: #c8c8c8;
    --ink: #1f3a50;
    --badge: #dfe8ef;
  }
  * { margin: 0; padding: 0; box-sizing: border-box; }
  html, body { width: 1200px; height: 763px; overflow: hidden; }
  body {
    position: relative;
    background: var(--backdrop);
    font-family: "Roboto", Arial, sans-serif;
    color: var(--ink);
  }
  .sheet, .card { position: absolute; background: var(--paper); overflow: hidden; }
  .sheet { left: 47px; top: 12px; width: 579px; height: 736px; box-shadow: 0 0 2px rgba(0,0,0,.25); }
  .card { left: 659px; width: 442px; height: 254px; border-radius: 9px; box-shadow: 0 1px 3px rgba(0,0,0,.3); }
  .card--front { top: 114px; }
  .card--back { top: 401px; background: var(--navy); }
  .wave { position: absolute; left: 0; top: 0; display: block; }
  .txt { position: absolute; white-space: nowrap; line-height: 1; }
  .wordmark { font-weight: 400; color: var(--navy); letter-spacing: -0.1px; }
  .sheet .wordmark { left: 38px; top: 64px; font-size: 15px; }
  .card--front .wordmark { left: 20px; top: 66px; font-size: 13.5px; }
  .card--back .wordmark { left: 0; right: 0; top: 124px; text-align: center; font-size: 28px; color: var(--paper); }
  .address { font-weight: 300; font-size: 9.6px; color: var(--paper); line-height: 13px; text-align: center; }
  .sheet .address { left: 382px; top: 50px; width: 160px; margin-left: -20px; }
  .contacts { list-style: none; }
  .contacts li { display: flex; align-items: center; gap: 2px; }
  .contacts svg { width: 8px; height: 8px; fill: var(--sky); flex: none; }
  .sheet .contacts { left: 36px; top: 674px; font-size: 9.6px; line-height: 13.5px; font-weight: 300; }
  .card--front .contacts { left: 19px; top: 196px; font-size: 11.2px; line-height: 16px; font-weight: 300; }
  .person { right: 21px; top: 31px; text-align: right; }
  .person__name { font-weight: 500; font-size: 15.5px; color: var(--sky); }
  .person__role { font-size: 11px; color: var(--paper); margin-top: 4px; }
  .card--front .address { right: 20px; top: 215px; text-align: right; color: var(--ink); font-size: 10.4px; line-height: 14px; }
  .affiliations { position: absolute; display: flex; gap: 8px; }
  .affiliations span { display: block; background: var(--badge); border-radius: 3px; }
  .sheet .affiliations { right: 38px; top: 674px; }
  .sheet .affiliations span { width: 40px; height: 40px; }
  .card--front .affiliations { right: 20px; top: 150px; gap: 6px; }
  .card--front .affiliations span { width: 30px; height: 30px; }
</style>
</head>
<body>

<section class="sheet letterhead">
  <svg class="wave" width="579" height="96" viewBox="0 0 965 160">
    <path fill="#4fa7de" d="M0,0 H965 V92 C870,128 780,148 700,145 C560,138 430,68 250,64 C160,63 90,80 0,98 Z"/>
    <path fill="#022c45" d="M0,0 H965 V70 C870,110 780,130 700,127 C560,120 430,60 250,62 C160,63 90,80 0,98 Z"/>
  </svg>
  <div class="txt wordmark">The Brightwater Joint Centre</div>
  <div class="txt address">48 Harrow Glen Parkway<br>Suite 310, Ashcombe, MI 48921</div>
  <ul class="txt contacts">
    <li><svg viewBox="0 0 10 10"><path d="M2 0.5 L3.8 2.6 L2.8 3.8 C3.5 5.3 4.7 6.5 6.2 7.2 L7.4 6.2 L9.5 8 L8.2 9.5 C4.3 9 1 5.7 0.5 1.8 Z"/></svg>555 014 2270</li>
    <li><svg viewBox="0 0 10 10"><path d="M0 2 H10 V8 H0 Z M0.6 2.4 L5 5.6 L9.4 2.4" stroke="#fff" stroke-width="0.8"/></svg>info@brightwaterjoint.com</li>
    <li><svg viewBox="0 0 10 10"><circle cx="5" cy="5" r="4.6"/><path d="M0.5 5 H9.5 M5 0.5 V9.5 M1.5 2.8 H8.5 M1.5 7.2 H8.5" stroke="#fff" stroke-width="0.6" fill="none"/></svg>www.brightwaterjoint.com</li>
  </ul>
  <div class="affiliations">
    <span role="img" aria-label="Crestmoor Lindell College of Surgeons badge"></span>
    <span role="img" aria-label="Varenwood Bone Health Association badge"></span>
  </div>
</section>

<section class="card card--front">
  <svg class="wave" width="442" height="92" viewBox="0 0 736 153">
    <path fill="#4fa7de" d="M0,0 H736 V104 C680,125 640,150 590,150 C480,150 330,60 110,50 C70,50 30,62 0,78 Z"/>
    <path fill="#022c45" d="M0,0 H736 V104 C680,118 640,132 590,132 C480,132 330,55 110,50 C70,50 30,62 0,78 Z"/>
  </svg>
  <div class="txt person">
    <div class="person__name">Adrian Kelso</div>
    <div class="person__role">President</div>
  </div>
  <div class="txt wordmark">The Brightwater Joint Centre</div>
  <div class="affiliations">
    <span role="img" aria-label="Crestmoor Lindell College of Surgeons badge"></span>
    <span role="img" aria-label="Varenwood Bone Health Association badge"></span>
  </div>
  <ul class="txt contacts">
    <li><svg viewBox="0 0 10 10"><path d="M2 0.5 L3.8 2.6 L2.8 3.8 C3.5 5.3 4.7 6.5 6.2 7.2 L7.4 6.2 L9.5 8 L8.2 9.5 C4.3 9 1 5.7 0.5 1.8 Z"/></svg>555 014 2270</li>
    <li><svg viewBox="0 0 10 10"><path d="M0 2 H10 V8 H0 Z M0.6 2.4 L5 5.6 L9.4 2.4" stroke="#fff" stroke-width="0.8"/></svg>info@brightwaterjoint.com</li>
    <li><svg viewBox="0 0 10 10"><circle cx="5" cy="5" r="4.6"/><path d="M0.5 5 H9.5 M5 0.5 V9.5 M1.5 2.8 H8.5 M1.5 7.2 H8.5" stroke="#fff" stroke-width="0.6" fill="none"/></svg>www.brightwaterjoint.com</li>
  </ul>
  <div class="txt address">48 Harrow Glen Parkway<br>Suite 310, Ashcombe, MI 48921</div>
</section>

<section class="card card--back">
  <div class="txt wordmark">The Brightwater Joint Centre</div>
</section>

</body>
</html>
```